PWRPT design for Company

Project: Develop a pwrpt for QT7lx. This can be just a blank pwrpt with standard templates that we can use to build our content and solutions around.
Website: www.qt7lx.example
Color Pallet: Try to use the color schema from our website.
PWRPT Design Tips: While we are a research-based company, our primary target is schools and school districts. We say our work is RESEARCH, POLICY, AND PRACTICE. I would like images that represent “WHY” our research matters, i.e. students, teachers, and administrators. If you can use images and stock photos that represent students with diverse backgrounds, teachers that are diverse and clearly teaching, and administrators that run a school, university, etc. We are in the process of updating our website, but the color scheme will remain the same.
Additional Information:
We built, researched, and designed, www.brvo-kt.example .
We built, researched, and designed, http://67pwgamma.example/olar/index.html
Target Market(s)
EDUCATION
Industry/Entity Type
It Company
Look and feel

```html
<!DOCTYPE html>
<html lang="en">
<head>
<meta charset="utf-8">
<title>QT7lx – Welcome Slide</title>
<link href="https://fonts.googleapis.com/css2?family=Raleway:wght@400;700;800&display=swap" rel="stylesheet">
<style>
  :root {
    --orange: #f7931e;
    --orange-band: rgba(247, 147, 30, 0.93);
    --white: #ffffff;
    --ink-soft: #4a4a4a;
    --brand-grey: #5b6466;
    --footer-bar: #5a6163;
    --photo-light: #f2f3f4;
    --photo-mid: #dfe6ee;
    --photo-blue: #b9cde3;
  }
  html, body {
    margin: 0;
    padding: 0;
    overflow: hidden;
    background: var(--white);
  }
  .slide {
    position: relative;
    width: 1200px;
    height: 900px;
    overflow: hidden;
    font-family: "Raleway", sans-serif;
    background: var(--white);
  }
  .hero {
    position: absolute;
    left: 0;
    top: 0;
    width: 1200px;
    height: 735px;
    overflow: hidden;
  }
  .hero-photo {
    position: absolute;
    inset: 0;
    background:
      radial-gradient(ellipse 420px 520px at 120px 260px, var(--photo-blue) 0%, rgba(185,205,227,0) 70%),
      radial-gradient(ellipse 380px 600px at 1080px 420px, #e8eef5 0%, rgba(232,238,245,0) 75%),
      linear-gradient(120deg, var(--photo-mid) 0%, var(--photo-light) 45%, #ececec 100%);
  }
  .hero-band {
    position: absolute;
    inset: 0;
  }
  .hero-title {
    position: absolute;
    left: 260px;
    width: 500px;
    text-align: center;
    color: var(--white);
    margin: 0;
  }
  .hero-title.welcome {
    top: 276px;
    font-size: 57px;
    font-weight: 800;
    letter-spacing: 1px;
  }
  .hero-title.program {
    top: 372px;
    font-size: 30px;
    font-weight: 700;
  }
  .hero-title.date {
    top: 424px;
    font-size: 25px;
    font-weight: 700;
  }
  .footer {
    position: absolute;
    left: 0;
    top: 735px;
    width: 1200px;
    height: 147px;
    background: var(--white);
  }
  .legal {
    position: absolute;
    left: 40px;
    top: 54px;
    width: 700px;
    margin: 0;
    font-size: 15.5px;
    line-height: 26px;
    font-weight: 400;
    color: var(--ink-soft);
  }
  .brand {
    position: absolute;
    right: 40px;
    top: 50px;
    display: flex;
    align-items: center;
    gap: 16px;
  }
  .brand-mark {
    width: 34px;
    height: 34px;
    background: var(--orange);
  }
  .brand-name {
    font-size: 40px;
    font-weight: 700;
    line-height: 1;
    color: var(--brand-grey);
  }
  .footer-bar {
    position: absolute;
    left: 0;
    top: 882px;
    width: 1200px;
    height: 18px;
    background: var(--footer-bar);
  }
</style>
</head>
<body>
<main class="slide">
  <section class="hero">
    <div class="hero-photo" role="img" aria-label="Photo of a person in a light blue shirt working at a desk with a laptop and an open browser screen"></div>
    <svg class="hero-band" width="1200" height="735" viewBox="0 0 1200 735" aria-hidden="true">
      <polygon points="368,0 938,0 698,735 128,735" fill="var(--orange-band)"/>
    </svg>
    <h1 class="hero-title welcome">WELCOME</h1>
    <p class="hero-title program">Route2Futures (R2F)</p>
    <p class="hero-title date">August 21st, 2017</p>
  </section>

  <footer class="footer">
    <p class="legal">© 2017 All rights reserved. Contains confidential and proprietary information and may<br>not be disclosed or reproduced without&nbsp; the prior written consent of QT7lx</p>
    <div class="brand">
      <span class="brand-mark" aria-hidden="true"></span>
      <span class="brand-name">QT7lx</span>
    </div>
  </footer>
  <div class="footer-bar"></div>
</main>
</body>
</html>
```